New business card/stationary for a consulting company

I am looking for a clean and very professional looking business card for my consulting company as well as corresponding stationary. I am uploading our logo. I like simple and powerful for the feel. No graphics but I am open on everything else. Below is my contact information but would like the final to be in a version I can add my employees information into and print. Thank you.

Daniel Whitcombe
dan@ferncliffadvisory.com
2870 North 9th Avenue, Summit Floor, Elm Ridge, Illinois 60531
www.ferncliffadvisory.com

Industry/Entity Type

Consulting

Contact Information for Business Card

Daniel Whitcombe
dan@ferncliffadvisory.com
www.ferncliffadvisory.com

Font styles to use
Serif
Sans Serif

Requirements
Must have
• Our logo and the business card details.
Nice to have
• our website www.ferncliffadvisory.com

```html
<!DOCTYPE html>
<html lang="en">
<head>
<meta charset="utf-8">
<title>Ferncliff Advisory – Business Card</title>
<link href="https://fonts.googleapis.com/css2?family=Questrial&family=Source+Sans+3:wght@400&display=swap" rel="stylesheet">
<style>
  :root {
    --navy: #06066b;
    --card-light: #efeeec;
    --page-bg: #e4e4e6;
    --white: #ffffff;
  }
  * { margin: 0; padding: 0; box-sizing: border-box; }
  html, body {
    width: 1200px;
    height: 900px;
    overflow: hidden;
    background: var(--page-bg);
  }
  .canvas {
    position: relative;
    width: 1200px;
    height: 900px;
  }
  .business-card {
    position: absolute;
    left: 150px;
    top: 172px;
    width: 900px;
    height: 556px;
    background: var(--card-light);
    box-shadow: 0 10px 30px rgba(0, 0, 0, 0.12);
    overflow: hidden;
  }
  .contact-panel {
    position: absolute;
    left: 0;
    top: 0;
    width: 428px;
    height: 100%;
    background: var(--navy);
    color: var(--white);
  }
  .divider-gap {
    position: absolute;
    left: 428px;
    top: 0;
    width: 8px;
    height: 100%;
    background: var(--white);
  }
  .divider-stripe {
    position: absolute;
    left: 436px;
    top: 0;
    width: 14px;
    height: 100%;
    background: var(--navy);
  }
  .holder-name {
    position: absolute;
    left: 51px;
    top: 72px;
    font-family: "Questrial", sans-serif;
    font-size: 26px;
    letter-spacing: 1.5px;
    text-transform: uppercase;
    white-space: nowrap;
  }
  .postal-address {
    position: absolute;
    left: 51px;
    top: 316px;
    font-family: "Source Sans 3", sans-serif;
    font-style: normal;
    font-size: 23px;
    line-height: 33px;
  }
  .contact-lines {
    position: absolute;
    left: 51px;
    top: 432px;
    list-style: none;
    font-family: "Source Sans 3", sans-serif;
    font-size: 23px;
    line-height: 32px;
  }
  .contact-lines li {
    display: flex;
    align-items: center;
    gap: 8px;
    white-space: nowrap;
  }
  .contact-lines svg { width: 20px; height: 20px; flex: none; }
  .brand-block {
    position: absolute;
    left: 450px;
    top: 0;
    right: 0;
    height: 100%;
    display: flex;
    flex-direction: column;
    align-items: center;
    justify-content: center;
    gap: 18px;
    padding-top: 28px;
  }
  .brand-square {
    width: 44px;
    height: 44px;
    background: var(--navy);
  }
  .brand-name {
    font-family: "Questrial", sans-serif;
    font-size: 27px;
    letter-spacing: 1.5px;
    text-transform: uppercase;
    color: var(--navy);
    white-space: nowrap;
  }
</style>
</head>
<body>
<main class="canvas">
  <section class="business-card" aria-label="Business card">
    <div class="contact-panel">
      <h1 class="holder-name">Daniel Whitcombe</h1>
      <address class="postal-address">
        2870 North 9th Avenue,<br>
        Summit Floor, Elm Ridge,<br>
        Illinois 60531
      </address>
      <ul class="contact-lines">
        <li>
          <svg viewBox="0 0 20 20" aria-hidden="true">
            <rect x="2" y="5" width="16" height="11" fill="#fff"/>
            <path d="M2 5 L10 11 L18 5" fill="none" stroke="#06066b" stroke-width="1.5"/>
          </svg>
          dan@ferncliffadvisory.com
        </li>
        <li>
          <svg viewBox="0 0 20 20" aria-hidden="true">
            <circle cx="10" cy="10" r="8" fill="#fff"/>
            <path d="M2 10 H18 M10 2 C6 6 6 14 10 18 M10 2 C14 6 14 14 10 18" fill="none" stroke="#06066b" stroke-width="1.2"/>
          </svg>
          www.ferncliffadvisory.com
        </li>
      </ul>
    </div>
    <div class="divider-gap"></div>
    <div class="divider-stripe"></div>
    <div class="brand-block">
      <div class="brand-square"></div>
      <p class="brand-name">Ferncliff Advisory</p>
    </div>
  </section>
</main>
</body>
</html>
```